interior designer/stylist looking for a letter press business card to reflect the stylish work

Hello Designers,
I need a business card design for an company called Mosaic Interior Design. I'm aiming at the high end residential and private client market in London providing sleek simple interiors. I'd like my business card to be pinterest worthy and expensive looking, i want people to pin it and for it to have a sought after look, and want prospective customers to hire me as their interior designer as my card is so beautiful.
I love letter press design. I also like the use of colour/foil on the edge.
Colour combos & general things I like -
Black and White
Navy Blue and Gold
Neutral colours (muted palette of greys whites navys beiges)
White Marble & brass
Vorelle (fashion designer)
....also open to other suggestions....
Please dont take the pink in the attached photos too literally. i'd like the card to look more masculine than feminine.
I'd like Mosaic on one side in one font, with interior design underneath so one word will make the statement....... unless anyone has any other ideas, open to suggestions.
I'd like a really simple font and for the whole card to look very graphic.
my details -
Petra Wendlecombe
Interior Designer & Stylist
email petra@mosaicinteriordesign.co.uk
phone +447311584209
website wwww.mosaicinteriordesign.co.uk
GO GO GO!! EXCITED TO SEE THE OUTCOME!!
x P
Target Market(s)
High End Residential and private clients
Industry/Entity Type
Business
Contact Information for Business Card
Mosaic Interior Design & Styling
Petra Wendlecombe
phone +447311584209

```html
<!DOCTYPE html>
<html lang="en">
<head>
<meta charset="utf-8">
<title>Mosaic Interior Design &amp; Styling – Business Card</title>
<link rel="stylesheet" href="https://fonts.googleapis.com/css2?family=PT+Sans:wght@400;700&display=swap">
<style>
  :root {
    --backdrop: #5f5f5f;
    --divider: #8a8a8a;
    --card-stock: #f5f4f0;
    --foil-gold: #b8891a;
    --edge-gold: #d9c98c;
  }
  * { margin: 0; padding: 0; box-sizing: border-box; }
  html, body { width: 870px; height: 1200px; overflow: hidden; }
  body {
    background: var(--backdrop);
    display: flex;
    flex-direction: column;
    font-family: "PT Sans", sans-serif;
  }
  .card-side {
    height: 600px;
    display: flex;
    align-items: center;
    justify-content: center;
  }
  .card-side + .card-side { border-top: 1px solid var(--divider); }
  .card {
    width: 600px;
    height: 343px;
    background: var(--card-stock);
    border-bottom: 4px solid var(--edge-gold);
    border-right: 4px solid var(--edge-gold);
    color: var(--foil-gold);
    position: relative;
  }

  /* Front */
  .card-front {
    display: flex;
    align-items: center;
    justify-content: center;
  }
  .company-name {
    font-weight: 400;
    font-size: 26px;
    line-height: 1.2;
    letter-spacing: 0.5px;
    text-align: center;
  }

  /* Back */
  .identity {
    position: absolute;
    right: 312px;
    top: 128px;
    text-align: right;
  }
  .person-name {
    font-weight: 700;
    font-size: 19px;
    line-height: 1.1;
  }
  .person-role {
    font-size: 15px;
    line-height: 1.2;
  }
  .contact-list {
    position: absolute;
    left: 310px;
    top: 158px;
    list-style: none;
    font-size: 13.5px;
    line-height: 1.3;
  }
</style>
</head>
<body>
  <section class="card-side">
    <div class="card card-front">
      <div class="company-name">Mosaic Interior Design &amp; Styling</div>
    </div>
  </section>

  <section class="card-side">
    <div class="card card-back">
      <div class="identity">
        <div class="person-name">Petra Wendlecombe</div>
        <div class="person-role">Interior Designer &amp; Stylist</div>
      </div>
      <ul class="contact-list">
        <li>+447311584209</li>
        <li>petra@mosaicinteriordesign.co.uk</li>
        <li>www.mosaicinteriordesign.co.uk</li>
      </ul>
    </div>
  </section>
</body>
</html>
```